Business card design for my company.
I would like the card's background colour to be black. You can also see our web site to get an idea of our brand. https://www.tmwhomecrafting.com.au/
- Name
- Email

```html
<!DOCTYPE html>
<html lang="en">
<head>
<meta charset="utf-8">
<title>TMW Home Crafting – Business Card</title>
<link href="https://fonts.googleapis.com/css2?family=Montserrat:wght@400;600&display=swap" rel="stylesheet">
<style>
  :root {
    --stage: #2a2a2c;
    --card: #141414;
    --card-back-dark: #0b0b0b;
    --card-back-light: #3a3a3a;
    --brand-green: #1f9a46;
    --text-light: #f2f2f2;
  }
  html, body {
    margin: 0;
    width: 1200px;
    height: 874px;
    overflow: hidden;
    background: var(--stage);
    font-family: "Montserrat", sans-serif;
  }
  .canvas {
    position: relative;
    width: 1200px;
    height: 874px;
  }
  .card {
    position: absolute;
    left: 330px;
    width: 540px;
    height: 309px;
    border-radius: 18px;
    overflow: hidden;
    box-shadow: 0 8px 24px rgba(0,0,0,0.45);
  }
  .card--back { top: 100px; background: var(--card-back-dark); }
  .card--front { top: 455px; background: var(--card); }

  .pattern-fill {
    position: absolute;
    inset: 0;
    background: linear-gradient(135deg, var(--card-back-light) 0%, #1c1c1c 45%, var(--card-back-dark) 100%);
  }
  .brand-mark {
    position: absolute;
    left: 50%;
    top: 50%;
    transform: translate(-50%, -50%);
    display: flex;
    align-items: center;
    gap: 8px;
    padding: 8px 12px;
    background: var(--card-back-dark);
  }
  .brand-mark__square {
    width: 12px;
    height: 12px;
    background: var(--brand-green);
  }
  .brand-mark__name {
    color: var(--text-light);
    font-weight: 600;
    font-size: 15px;
    letter-spacing: 0.5px;
  }

  .identity {
    position: absolute;
    right: 300px;
    top: 118px;
    text-align: right;
  }
  .identity__name {
    color: var(--brand-green);
    font-weight: 600;
    font-size: 28px;
    margin: 0;
    white-space: nowrap;
  }
  .identity__role {
    color: var(--text-light);
    font-size: 15px;
    margin: 4px 0 0;
  }
  .divider {
    position: absolute;
    left: 258px;
    top: 112px;
    width: 2px;
    height: 70px;
    background: var(--brand-green);
  }
  .contacts {
    position: absolute;
    left: 276px;
    top: 112px;
    list-style: none;
    margin: 0;
    padding: 0;
  }
  .contacts li {
    display: flex;
    align-items: center;
    gap: 8px;
    color: var(--text-light);
    font-size: 14px;
    line-height: 24px;
    white-space: nowrap;
  }
  .contacts svg { width: 13px; height: 13px; fill: var(--brand-green); flex: none; }
</style>
</head>
<body>
<main class="canvas">
  <section class="card card--back">
    <div class="pattern-fill" role="img" aria-label="Repeating brand pattern in glossy black and grey"></div>
    <div class="brand-mark">
      <span class="brand-mark__square"></span>
      <span class="brand-mark__name">TMW Home Crafting</span>
    </div>
  </section>

  <section class="card card--front">
    <div class="identity">
      <h1 class="identity__name">Liam Carver</h1>
      <p class="identity__role">General Manager</p>
    </div>
    <div class="divider"></div>
    <ul class="contacts">
      <li>
        <svg viewBox="0 0 24 24"><path d="M6.6 10.8a15 15 0 0 0 6.6 6.6l2.2-2.2a1 1 0 0 1 1-.25 11.4 11.4 0 0 0 3.6.57 1 1 0 0 1 1 1V20a1 1 0 0 1-1 1A17 17 0 0 1 3 4a1 1 0 0 1 1-1h3.5a1 1 0 0 1 1 1c0 1.25.2 2.45.57 3.57a1 1 0 0 1-.25 1z"/></svg>
        0400 555 173
      </li>
      <li>
        <svg viewBox="0 0 24 24"><path d="M2 5h20v14H2z M2 5l10 8 10-8" fill="none" stroke="#1f9a46" stroke-width="2"/></svg>
        info@tmwhomecrafting.com.au
      </li>
      <li>
        <svg viewBox="0 0 24 24"><circle cx="12" cy="12" r="9" fill="none" stroke="#1f9a46" stroke-width="2"/><path d="M3 12h18M12 3c3 3 3 15 0 18M12 3c-3 3-3 15 0 18" fill="none" stroke="#1f9a46" stroke-width="1.6"/></svg>
        www.tmwhomecrafting.com.au
      </li>
    </ul>
  </section>
</main>
</body>
</html>
```